Need Amazing Website for Consulting Company

We need an amazing website design for a Human Resources Consulting Company. This will be geared towards a more professional crowd, but we don't want it to be overly corporate and stuffy: Just, clean and professional and amazing. Please use the video link below for further instruction.

http://clipharbor.net/v/kLm9PxQz

Thank You.

PS Logo file has been attached.

Target Market(s)

The target marketing is small business owners who have employees. These owners cant afford an in-house HR person so they would hire this client to consult and do the work for them.

Industry/Entity Type

It Company

Font styles to use
Sans Serif

Requirements
Must have
• Please watch video:

Must have spot for video on homepage.
Nice to have
• Clean, professional, but not overly corporate, we want a personal and fun feel to this site a bit to separate them from all the other executive type sites. This site should have some LIFE to it and reflect a local brand that is doing great things.
Should not have
• Should not be just a corporate site, should not be overly stuffy, should not be overly boring.

```html
<!DOCTYPE html>
<html lang="en">
<head>
<meta charset="utf-8">
<title>Mesa Ridge HR Consulting</title>
<link href="https://fonts.googleapis.com/css2?family=Lato:wght@400;700;900&family=Raleway:wght@300;400&display=swap" rel="stylesheet">
<style>
:root{
  --red:#c0202f;
  --red-dark:#a51a27;
  --ink:#222222;
  --panel:#262626;
  --panel-2:#1c1c1c;
  --white:#ffffff;
  --grey-band:#e4e4e4;
  --muted:#bdbdbd;
  --text:#333333;
}
*{box-sizing:border-box;margin:0;padding:0}
html,body{width:1154px;height:1200px;overflow:hidden}
body{position:relative;background:var(--white);font-family:"Lato",Arial,sans-serif;color:var(--text)}
.abs{position:absolute}

/* header */
.brand{left:204px;top:16px;width:150px;color:var(--ink);font-weight:900;font-size:16px;line-height:19px;text-transform:uppercase;letter-spacing:.5px;display:flex;align-items:center;gap:8px}
.brand-mark{width:14px;height:14px;background:var(--ink);flex:none}
.main-nav{left:0;top:89px;width:1154px;height:38px;background:linear-gradient(var(--red),var(--red-dark));display:flex;justify-content:center;align-items:center}
.main-nav a{color:var(--white);text-decoration:none;font-size:11px;font-weight:700;letter-spacing:1.3px;text-transform:uppercase;white-space:nowrap}
.main-nav .sep{color:#f0c0c5;margin:0 15px;font-size:11px}

/* hero */
.hero{left:0;top:127px;width:1154px;height:285px;background:linear-gradient(90deg,#8d8a86 0%,#c9c3bb 30%,#dcd6cc 60%,#6d8aa4 80%,#b7b2aa 100%)}
.video{left:204px;top:142px;width:452px;height:254px;background:linear-gradient(100deg,#eef1f4 0%,#dfe6ee 40%,#f4f4f4 75%,#e8e8e8 100%);overflow:hidden}
.video-tagline{left:265px;top:18px;font-family:"Raleway",Arial,sans-serif;font-weight:300;font-size:19px;line-height:24px;color:var(--red)}
.video-play{left:164px;top:94px}
.video-controls{left:18px;top:212px;width:416px;height:32px}
.about-panel{left:667px;top:142px;width:281px;height:254px;background:var(--panel-2);color:var(--white);padding:0 17px 8px;display:flex;flex-direction:column;overflow:hidden}
.about-panel h2{font-size:11px;font-weight:700;letter-spacing:1.4px;text-transform:uppercase;white-space:nowrap;margin-top:12px;padding-bottom:11px;border-bottom:1px solid #3a3a3a}
.about-photo{margin-top:12px;height:87px;flex:none;background:linear-gradient(90deg,#e9e3dc,#b9c3cc 60%,#5d6775)}
.about-panel p{margin-top:10px;font-size:10.5px;line-height:13.5px;text-align:justify}
.about-values{margin-top:auto;display:flex;justify-content:space-between;font-size:12px;padding-top:6px;border-top:1px solid #3a3a3a;white-space:nowrap}
.about-values i{font-style:normal;color:var(--muted);font-size:8px;line-height:14px}

/* feature cards */
.card{top:460px;width:177px;height:308px;background:var(--panel);color:var(--white)}
.card-tab{position:absolute;left:0;top:0;width:156px;height:34px;background:var(--red);font-size:10.5px;font-weight:700;letter-spacing:1px;text-transform:uppercase;white-space:nowrap;padding:11px 0 0 11px}
.card-photo{position:absolute;left:10px;top:44px;width:157px;height:152px}
.card-body{position:absolute;left:8px;top:208px;width:161px;font-size:10.5px;line-height:12px;text-align:justify}
.card-body.list{text-align:left;font-size:10px}
.card-body.list span{display:block;margin-bottom:9px;white-space:nowrap}
.card-more{position:absolute;right:0;bottom:0;width:66px;height:22px;background:#111;color:var(--red);font-size:6.5px;font-weight:900;letter-spacing:.6px;text-transform:uppercase;text-align:center;line-height:22px}

/* testimonial band */
.band{left:0;top:786px;width:1154px;height:174px;background:var(--grey-band)}
.testimonial{left:205px;top:814px;width:408px;height:116px;background:#ededed;border:1px solid #d2d2d2;box-shadow:0 2px 3px rgba(0,0,0,.15)}
.testimonial-photo{left:13px;top:22px;width:80px;height:80px;background:linear-gradient(#cfd3d6,#8b8f93);border:1px solid #aaa}
.testimonial-quote{left:102px;top:20px;width:295px;font-size:10.5px;line-height:12px;color:#444;text-align:justify}
.testimonial-by{right:12px;top:96px;font-size:9.5px;color:#333;white-space:nowrap}
.testimonial-by b{margin-right:10px}
.clients-title{left:668px;top:812px;width:232px;text-align:center;font-size:11px;letter-spacing:1.6px;font-weight:700;color:#222}
.clients-frame{left:668px;top:848px;width:232px;height:80px;background:#d2d2d2;padding:9px}
.clients-logo{width:100%;height:100%;background:var(--white);display:flex;align-items:center;justify-content:center;font-size:14px;font-weight:900;color:var(--ink);letter-spacing:.5px}
.slide-arrow{top:875px}

/* footer */
.hatch{left:0;top:982px;width:1154px;height:14px;background:repeating-linear-gradient(45deg,#cfcfcf 0 2px,#f2f2f2 2px 4px)}
.footer{left:0;top:996px;width:1154px;height:168px;background:var(--panel);color:var(--white)}
.footer h3{position:absolute;top:24px;font-size:11px;font-weight:700;letter-spacing:1.5px;text-transform:uppercase}
.footer-links{position:absolute;left:222px;top:52px;width:210px;list-style:none}
.footer-links li{font-size:10.5px;height:23px;line-height:20px;border-bottom:1px solid #383838}
.contact-list{position:absolute;left:480px;top:52px;width:205px;list-style:none}
.contact-list li{font-size:10.5px;line-height:18px;min-height:23px;border-bottom:1px solid #383838;display:flex;gap:10px;align-items:flex-start}
.contact-list li:last-child{border:none}
.contact-list svg{flex:none;margin-top:4px}
.social{position:absolute;left:787px;top:56px;display:flex;gap:6px}
.social span{height:26px;padding:0 6px;background:var(--white);color:var(--ink);border-radius:4px;font-size:9.5px;font-weight:700;line-height:26px}
.social .mail{width:26px;padding:0;display:flex;align-items:center;justify-content:center}
.copyright{left:0;top:1164px;width:1154px;height:36px;background:var(--red);color:var(--white);font-size:11px;text-align:center;line-height:36px}
</style>
</head>
<body>

<header>
  <div class="abs brand"><span class="brand-mark"></span>Mesa Ridge HR Consulting</div>
  <nav class="abs main-nav">
    <a href="#">Home</a><span class="sep">/</span>
    <a href="#">Ethos</a><span class="sep">/</span>
    <a href="#">Services</a><span class="sep">/</span>
    <a href="#">News &amp; Media</a><span class="sep">/</span>
    <a href="#">Clientele</a><span class="sep">/</span>
    <a href="#">Our Unique Offerings</a><span class="sep">/</span>
    <a href="#">HR Solutions</a>
  </nav>
</header>

<section class="abs hero" role="img" aria-label="Blurred bright office interior"></section>

<section class="abs video" role="img" aria-label="Video still: relaxed professional leaning back in a chair">
  <div class="abs video-tagline">Relaxed!.<br>While we do the job</div>
  <svg class="abs video-play" width="66" height="66" viewBox="0 0 66 66">
    <circle cx="33" cy="33" r="31" fill="none" stroke="#c0202f" stroke-width="2"/>
    <path d="M26 21 L46 33 L26 45 Z" fill="none" stroke="#c0202f" stroke-width="2" stroke-linejoin="round"/>
  </svg>
  <svg class="abs video-controls" width="416" height="32" viewBox="0 0 416 32">
    <rect x="0" y="0" width="50" height="30" rx="3" fill="#3a3a3a"/>
    <path d="M20 8 L32 15 L20 22 Z" fill="#fff"/>
    <rect x="54" y="4" width="292" height="22" rx="2" fill="#2b2b2b" opacity=".85"/>
    <rect x="60" y="12" width="220" height="6" fill="#555"/>
    <rect x="60" y="12" width="66" height="6" fill="#2aa0e0"/>
    <g fill="#2aa0e0">
      <rect x="353" y="11" width="2" height="8"/><rect x="357" y="11" width="2" height="8"/><rect x="361" y="11" width="2" height="8"/><rect x="365" y="11" width="2" height="8"/><rect x="369" y="11" width="2" height="8"/>
    </g>
    <text x="378" y="20" fill="#2aa0e0" font-family="Lato,sans-serif" font-weight="900" font-style="italic" font-size="11">HD</text>
    <path d="M400 10 L408 18 M408 10 L400 18" stroke="#fff" stroke-width="2"/>
  </svg>
</section>

<aside class="abs about-panel">
  <h2>We are a different kinf of agency</h2>
  <div class="about-photo" role="img" aria-label="Smiling businesswoman with colleagues in the background"></div>
  <p>Mesa Ridge HR Consulting, LLC. (MRHRC) is an experienced consulting agency that is committed to providing businesses with effective and efficient Human Resources support by developing partner-ships to meet company's individual needs.</p>
  <div class="about-values"><span>EFFECTIVE</span><i>◆</i><span>EXPERIENCED</span><i>◆</i><span>EFFICIENT</span></div>
</aside>

<section>
  <article class="abs card" style="left:204px">
    <div class="card-tab">Service Areas</div>
    <div class="card-photo" role="img" aria-label="Suit and tie with a wrench in the breast pocket" style="background:linear-gradient(120deg,#d8d8d8,#6e6e6e 55%,#3a3a3a)"></div>
    <p class="card-body">Maecenas eu placerat ante. Fusce ut neque justo, et aliquet enim. In hac habitasse platea dictumst. Nullam commodo neque erat, vitae facilisis erat.</p>
    <div class="card-more">Learn more</div>
  </article>
  <article class="abs card" style="left:392px">
    <div class="card-tab">Thought Leadership</div>
    <div class="card-photo" role="img" aria-label="Businesswoman writing on a glass board" style="background:linear-gradient(90deg,#f1f1f1,#d9dbdd 50%,#b9bdc2)"></div>
    <p class="card-body">Maecenas eu placerat ante. Fusce ut neque justo, et aliquet enim. In hac habitasse platea dictumst. Nullam commodo neque erat, vitae facilisis erat.</p>
    <div class="card-more">Learn more</div>
  </article>
  <article class="abs card" style="left:583px">
    <div class="card-tab">HR Solutions</div>
    <div class="card-photo" role="img" aria-label="Hand holding a puzzle piece against a blue sky" style="background:linear-gradient(#3f7fc4,#8db8de 55%,#a6b98a)"></div>
    <p class="card-body list"><span>HR solution for the PUBLIC SECTOR</span><span>HR solution for the CORPORATE</span><span>ROLE BASED HR solution for the</span></p>
    <div class="card-more">Learn more</div>
  </article>
  <article class="abs card" style="left:773px">
    <div class="card-tab">News &amp; Media</div>
    <div class="card-photo" role="img" aria-label="Person working on a laptop surrounded by newspapers" style="background:linear-gradient(135deg,#c9c2b8,#8f8a84 50%,#d7d1c8)"></div>
    <p class="card-body">Maecenas eu placerat ante. Fusce ut neque justo, et aliquet enim. In hac habitasse platea dictumst. Nullam commodo neque erat, vitae facilisis erat.</p>
    <div class="card-more">Learn more</div>
  </article>
</section>

<section class="abs band"></section>
<blockquote class="abs testimonial">
  <div class="abs testimonial-photo" role="img" aria-label="Portrait of a client"></div>
  <p class="abs testimonial-quote">Maecenas eu placerat ante. Fusce ut neque justo, et aliquet enim. In hac habitasse platea dictumst. Nullam commodo neque erat, vitae facilisis erat.Maecenas eu placerat ante. Fusce ut neque justo, et aliquet enim. In hac habitasse platea dictumst. Nullam commodo neque erat, vitae facilisis erat.</p>
  <p class="abs testimonial-by"><b>Alan Reyes /</b> 14 Mar 2050 @ 11:07am</p>
</blockquote>
<h2 class="abs clients-title">OUR SUCCESSFUL CLIENTS</h2>
<div class="abs clients-frame"><div class="clients-logo">BRIGHTWAVE STUDIOS</div></div>
<svg class="abs slide-arrow" style="left:633px" width="28" height="28" viewBox="0 0 28 28"><circle cx="14" cy="14" r="13" fill="#fff" stroke="#ccc"/><path d="M16 8 L10 14 L16 20" fill="none" stroke="#999" stroke-width="2.5"/></svg>
<svg class="abs slide-arrow" style="left:910px" width="28" height="28" viewBox="0 0 28 28"><circle cx="14" cy="14" r="13" fill="#fff" stroke="#ccc"/><path d="M12 8 L18 14 L12 20" fill="none" stroke="#999" stroke-width="2.5"/></svg>

<div class="abs hatch"></div>
<footer class="abs footer">
  <h3 style="left:222px">About Us</h3>
  <ul class="footer-links">
    <li>Frequently Asked Questions</li>
    <li>HR Services</li>
    <li>Carrer with us</li>
    <li>Why Choose Us</li>
    <li style="border:none">Our Company</li>
  </ul>
  <h3 style="left:480px">Contact Us</h3>
  <ul class="contact-list">
    <li><svg width="12" height="9" viewBox="0 0 12 9"><rect x=".5" y=".5" width="11" height="8" fill="none" stroke="#fff"/><path d="M.5 .5 L6 5 L11.5 .5" fill="none" stroke="#fff"/></svg>info@mesaridgehr.com</li>
    <li><svg width="12" height="12" viewBox="0 0 12 12"><path d="M2 1 L4.5 1 L5.5 4 L4 5 Q5 7.5 7 8 L8 6.5 L11 7.5 L11 10 Q5 11 1 3 Z" fill="#fff"/></svg>(505) 555-0148</li>
    <li><svg width="12" height="13" viewBox="0 0 12 13"><path d="M6 12 Q1 6 1 4.5 A5 5 0 0 1 11 4.5 Q11 6 6 12 Z" fill="#fff"/><circle cx="6" cy="4.5" r="1.8" fill="#262626"/></svg><span>MRHRC, LLC.<br>P.O. Box 40912<br>Santa Fe, NM 87504</span></li>
  </ul>
  <h3 style="left:787px">Get Social</h3>
  <div class="social">
    <span>Chirp</span><span>Friendly</span><span>Worknet</span>
    <span class="mail"><svg width="16" height="11" viewBox="0 0 16 11"><rect x=".8" y=".8" width="14.4" height="9.4" fill="none" stroke="#222" stroke-width="1.5"/><path d="M.8 .8 L8 6 L15.2 .8" fill="none" stroke="#222" stroke-width="1.5"/></svg></span>
  </div>
</footer>
<div class="abs copyright">Mesa Ridge HR Consulting, LLC, All rights reserved</div>

</body>
</html>
```